Business Card for Industrial Distributor

We need a business card design for an industrial distributor. We sell machine parts for the manufacturing and oil industry. We would like the cards to look clean and modern but with a touch of industry.

Our colors are blue/white.

Please feel free to visit our website www.korvelpartsco.com

Target Market(s)

mexican manufacturers in the automobile/aerospace industry

Industry/Entity Type

Industrial

Colors
ffffff
0555a3

```html
<!DOCTYPE html>
<html lang="en">
<head>
<meta charset="UTF-8">
<title>Korvel Business Card</title>
<link rel="stylesheet" href="https://fonts.googleapis.com/css2?family=Open+Sans:wght@400;600;700;800&display=swap">
<style>
  :root {
    --brand-navy: #2a3b94;
    --brand-blue: #0555a3;
    --accent-blue: #1a78c2;
    --paper: #ffffff;
    --ink: #333333;
    --stage: #eceef1;
  }
  * { margin: 0; padding: 0; box-sizing: border-box; }
  html, body {
    width: 1200px;
    height: 900px;
    overflow: hidden;
    background: var(--stage);
    font-family: "Open Sans", sans-serif;
  }
  .canvas { position: relative; width: 1200px; height: 900px; }
  .card {
    position: absolute;
    width: 560px;
    height: 320px;
    border-radius: 3px;
    overflow: hidden;
    box-shadow: 0 6px 18px rgba(0,0,0,0.18);
  }
  /* Back side */
  .card-back {
    left: 140px;
    top: 110px;
    background: var(--brand-navy);
    color: var(--paper);
  }
  .brand-name {
    position: absolute;
    left: 0; right: 0; top: 106px;
    text-align: center;
    font-weight: 800;
    font-size: 60px;
    letter-spacing: 1px;
    line-height: 1;
    color: var(--paper);
  }
  .back-url {
    position: absolute;
    left: 0; right: 0; top: 222px;
    text-align: center;
    font-size: 14px;
    letter-spacing: 0.3px;
  }
  /* Front side */
  .card-front {
    left: 500px;
    top: 470px;
    background: var(--paper);
  }
  .front-wave { position: absolute; inset: 0; }
  .front-brand {
    position: absolute;
    right: 40px; top: 56px;
    font-weight: 800;
    font-size: 34px;
    line-height: 1;
    letter-spacing: 0.5px;
    color: var(--brand-navy);
  }
  .holder { position: absolute; left: 44px; top: 62px; }
  .holder-name {
    font-weight: 700;
    font-size: 19px;
    color: var(--brand-navy);
    line-height: 1.1;
  }
  .holder-title { font-size: 13px; color: var(--ink); }
  .contact-list {
    position: absolute;
    left: 44px; top: 120px;
    list-style: none;
    font-size: 15px;
    color: var(--ink);
    line-height: 20px;
  }
  .contact-list li { display: flex; align-items: center; gap: 10px; }
  .contact-list svg { width: 12px; height: 12px; fill: var(--brand-navy); flex: none; }
  .address {
    position: absolute;
    left: 44px; top: 200px;
    font-size: 15px;
    color: var(--ink);
    line-height: 20px;
  }
  .front-url {
    position: absolute;
    right: 26px; top: 218px;
    font-size: 12px;
    color: var(--paper);
  }
</style>
</head>
<body>
<main class="canvas">
  <section class="card card-back" aria-label="Card back">
    <p class="brand-name">Korvel</p>
    <p class="back-url">www.korvelpartsco.com</p>
  </section>

  <section class="card card-front" aria-label="Card front">
    <svg class="front-wave" viewBox="0 0 560 320" preserveAspectRatio="none" aria-hidden="true">
      <path d="M0,300 C150,300 310,262 410,190 C465,150 520,135 560,128 L560,320 L0,320 Z" fill="var(--brand-navy)"/>
      <path d="M0,268 C140,272 280,246 380,188 C300,250 150,282 0,286 Z" fill="var(--accent-blue)"/>
      <path d="M0,286 C150,282 300,250 380,188 C310,255 160,292 0,294 Z" fill="var(--paper)"/>
    </svg>
    <p class="front-brand">Korvel</p>
    <div class="holder">
      <p class="holder-name">Daniel Morrow</p>
      <p class="holder-title">Managing Director</p>
    </div>
    <ul class="contact-list">
      <li><svg viewBox="0 0 12 12"><path d="M1 4 C3 1 9 1 11 4 L9 5 L8 4 C7 3.5 5 3.5 4 4 L3 5 Z M3 6 H9 L10 10 H2 Z"/></svg>(044) 555 210 347</li>
      <li><svg viewBox="0 0 12 12"><path d="M3 0 H9 V12 H3 Z M4 1.5 V9.5 H8 V1.5 Z" fill-rule="evenodd"/></svg>(044)555210348</li>
      <li><svg viewBox="0 0 12 12"><path d="M0 2 H12 V10 H0 Z M1 3 L6 7 L11 3" fill-rule="evenodd"/></svg>info@korvelpartsco.com</li>
    </ul>
    <p class="address">12345,your address goes here,<br>country name,12345</p>
    <p class="front-url">www.korvelpartsco.com</p>
  </section>
</main>
</body>
</html>
```